Quorva - corporate Business Card

We need a good look and innovative business card for a new start up company based in Los Angeles called "Quorva". We are in a payment business, including payment card, app, and ewallet. We are expert in online payment and Card not present (CNP) transaction.
We need an innovative, modern business card.

Our logo font is Aero Matics

Target Market(s)

Startup - Bank - Online Payment - Card Manufacturing

Industry/Entity Type

Startup

Contact Information for Business Card

phone: 555 014 7396 - Address: 4172 Marlowe blvd, Larkmont City, CA 90299

Requirements
Must have
• Message: innovative, professional, expert, high tech, trust, online payment expert, security
Nice to have
• no comment
Should not have
• no Comment

```html
<!DOCTYPE html>
<html lang="en">
<head>
<meta charset="utf-8">
<title>Quorva — Business Card</title>
<link rel="stylesheet" href="https://fonts.googleapis.com/css2?family=Montserrat:wght@400;500;700&display=swap">
<style>
  :root {
    --bg: #1b1b1d;
    --card-red: #b81f2e;
    --card-red-light: #c42a38;
    --white: #ffffff;
    --disc-grey: #e6e6e8;
    --text-soft: rgba(255,255,255,0.85);
  }
  * { box-sizing: border-box; margin: 0; padding: 0; }
  html, body { width: 1200px; height: 1000px; overflow: hidden; }
  body {
    background: var(--bg);
    font-family: "Montserrat", Arial, sans-serif;
    position: relative;
  }
  .card {
    position: absolute;
    left: 250px;
    width: 700px;
    height: 400px;
    border-radius: 34px;
    background: linear-gradient(120deg, var(--card-red-light), var(--card-red) 60%);
    overflow: hidden;
    color: var(--white);
  }
  .card--front { top: 60px; }
  .card--back { top: 540px; }

  .brand {
    display: flex;
    align-items: center;
    gap: 14px;
  }
  .brand__dot {
    width: 78px; height: 78px;
    border-radius: 50%;
    background: var(--white);
    flex: none;
  }
  .brand__name {
    font-weight: 700;
    font-size: 74px;
    letter-spacing: 1px;
    line-height: 1;
    text-transform: lowercase;
    white-space: nowrap;
  }
  .card--front .brand {
    position: absolute;
    left: 50%; top: 150px;
    transform: translateX(-50%);
  }
  .front__web {
    position: absolute;
    left: 0; right: 0; bottom: 70px;
    text-align: center;
    font-size: 15px;
    letter-spacing: 5px;
    color: var(--text-soft);
  }

  .badge {
    position: absolute;
    right: 24px; top: 26px;
    width: 348px; height: 348px;
    border-radius: 50%;
    background: var(--disc-grey);
    border: 22px solid var(--white);
    display: flex; align-items: center; justify-content: center;
  }
  .badge .brand { gap: 10px; }
  .badge .brand__dot { width: 54px; height: 54px; background: var(--card-red); }
  .badge .brand__name { font-size: 50px; color: var(--card-red); }
  .person {
    position: absolute;
    left: 60px; top: 110px;
  }
  .person__name {
    font-size: 30px;
    font-weight: 700;
    letter-spacing: 0.5px;
    text-transform: uppercase;
    white-space: nowrap;
  }
  .person__role { font-size: 19px; margin-top: 4px; }
  .contacts {
    position: absolute;
    left: 60px; top: 215px;
    list-style: none;
    font-size: 16px;
  }
  .contacts li { display: flex; align-items: center; gap: 12px; height: 22px; }
  .contacts svg { width: 13px; height: 13px; fill: var(--white); flex: none; }
  .address {
    position: absolute;
    left: 60px; top: 310px;
    font-style: normal;
    font-size: 16px;
    line-height: 1.35;
  }
</style>
</head>
<body>
  <section class="card card--front" aria-label="Business card front">
    <div class="brand">
      <span class="brand__dot"></span>
      <span class="brand__name">quorva</span>
    </div>
    <p class="front__web">www.quorva.com</p>
  </section>

  <section class="card card--back" aria-label="Business card back">
    <div class="person">
      <h1 class="person__name">Daniel Brooks</h1>
      <p class="person__role">Ceo &amp; Founder</p>
    </div>
    <ul class="contacts">
      <li>
        <svg viewBox="0 0 24 24"><path d="M6.6 10.8a15 15 0 0 0 6.6 6.6l2.2-2.2a1 1 0 0 1 1-.25 11.4 11.4 0 0 0 3.6.57 1 1 0 0 1 1 1V20a1 1 0 0 1-1 1A17 17 0 0 1 3 4a1 1 0 0 1 1-1h3.5a1 1 0 0 1 1 1c0 1.25.2 2.45.57 3.57a1 1 0 0 1-.25 1z"/></svg>
        <span>555 014 7396</span>
      </li>
      <li>
        <svg viewBox="0 0 24 24"><path d="M2 5h20v14H2z M2 5l10 8 10-8" fill="none" stroke="#fff" stroke-width="2"/></svg>
        <span>hello@quorva.com</span>
      </li>
      <li>
        <svg viewBox="0 0 24 24"><circle cx="12" cy="12" r="10"/></svg>
        <span>www.quorva.com</span>
      </li>
    </ul>
    <address class="address">4172 Marlowe blvd<br>Larkmont City, CA 90299</address>
    <div class="badge">
      <div class="brand">
        <span class="brand__dot"></span>
        <span class="brand__name">quorva</span>
      </div>
    </div>
  </section>
</body>
</html>
```